A Modern & Sleek "Coming Soon" Page for an A.I Recruiting App

For the “Coming Soon” website, a simple background with no people in it. I've attached an A.I image of what the page should generally look like.

- A single mobile phone as the main focus where the user actually clicks on the, “notify me” button (after entering their email address).
- In the background where the pillars/columns are seen in the example, should be subtle pad locks that are in their opened position with a key inside the lock. I've attached images to try to illustrate this idea, but they are far away in style from what I'm looking for.

SLOGAN: Unlocking the power of meaningful connections
LOGO/TITLE: Should be the name as shown in image with only the name "KelvoLink" on it
COLORS: Purplish/blue hues. Should not be too feminine
NOTE: The user should only click once when signing up/entering their email.

Product: A recruiting platform that matches employers/employees with A.I. and prioritizing cultural fit/values system before skills. The industry we are tackling first is the caregiving industry (nannies, tutors, elderly). All users will be background screened and that info lives on the blockchain. All users will have the option to review and be reviewed/rated.

```html
<!DOCTYPE html>
<html lang="en">
<head>
<meta charset="UTF-8">
<title>Kelvo Link — Coming Soon</title>
<link href="https://fonts.googleapis.com/css2?family=Lato:wght@700;900&display=swap" rel="stylesheet">
<style>
  :root {
    --bg-deep: #141617;
    --bg-mid: #222526;
    --bg-light: #2c2f31;
    --text-main: #ffffff;
    --button-bg: #ffffff;
    --button-text: #111314;
    --phone-violet: #4a2275;
    --phone-dark: #241236;
    --lock-steel: #6d7275;
    --lock-dark: #2a2d2f;
  }
  * { margin: 0; padding: 0; box-sizing: border-box; }
  html, body {
    width: 1200px;
    height: 807px;
    overflow: hidden;
    background: var(--bg-deep);
  }
  .page {
    position: relative;
    width: 1200px;
    height: 807px;
    overflow: hidden;
    font-family: "Lato", sans-serif;
    color: var(--text-main);
    background:
      radial-gradient(ellipse at 75% 30%, var(--bg-light) 0%, transparent 55%),
      radial-gradient(ellipse at 20% 60%, var(--bg-mid) 0%, transparent 60%),
      linear-gradient(180deg, var(--bg-mid) 0%, var(--bg-deep) 100%);
  }
  .menu-icon {
    position: absolute;
    left: 1092px;
    top: 46px;
    width: 48px;
    height: 36px;
  }
  .hero-phone {
    position: absolute;
    left: 165px;
    top: 85px;
    width: 378px;
    height: 623px;
    border-radius: 40px;
    transform: rotate(-6deg);
    background: linear-gradient(160deg, var(--phone-violet) 0%, var(--phone-dark) 100%);
  }
  .hero-lock {
    position: absolute;
    left: 681px;
    top: 304px;
    width: 343px;
    height: 446px;
    border-radius: 30px;
    background: radial-gradient(ellipse at 55% 60%, var(--lock-steel) 0%, var(--lock-dark) 60%, transparent 80%);
  }
  .hero-copy {
    position: absolute;
    left: 568px;
    top: 150px;
  }
  .brand-title {
    font-size: 73px;
    font-weight: 700;
    line-height: 1;
    letter-spacing: -0.5px;
  }
  .slogan {
    margin-top: 50px;
    margin-left: 8px;
    font-size: 23px;
    font-weight: 700;
  }
  .signup-button {
    display: block;
    margin-top: 48px;
    margin-left: 4px;
    width: 167px;
    height: 60px;
    border: none;
    background: var(--button-bg);
    color: var(--button-text);
    font-family: "Lato", sans-serif;
    font-size: 23px;
    font-weight: 700;
    cursor: pointer;
  }
  .footer-note {
    position: absolute;
    left: 0;
    right: 0;
    top: 756px;
    text-align: center;
    font-size: 23px;
    font-weight: 700;
  }
</style>
</head>
<body>
  <main class="page">
    <svg class="menu-icon" viewBox="0 0 48 36" aria-label="Menu">
      <line x1="3" y1="3" x2="46" y2="3" stroke="#ffffff" stroke-width="4" stroke-linecap="round"/>
      <line x1="10" y1="18" x2="46" y2="18" stroke="#ffffff" stroke-width="4" stroke-linecap="round"/>
      <line x1="18" y1="33" x2="46" y2="33" stroke="#ffffff" stroke-width="4" stroke-linecap="round"/>
    </svg>

    <div class="hero-phone" role="img" aria-label="Purple smartphone showing the app name, slogan and a notify me button"></div>

    <div class="hero-lock" role="img" aria-label="Open silver padlock with a glowing key inserted"></div>

    <section class="hero-copy">
      <h1 class="brand-title">Kelvo Link</h1>
      <p class="slogan">Unlocking the power of meaningful connections</p>
      <button class="signup-button" type="button">Sign Up</button>
    </section>

    <footer class="footer-note">Copyrights@2024.Kelvo Link.All Rights Reserved</footer>
  </main>
</body>
</html>
```